Web Developer Needs a Business Card Design

I need a personal business card design that represents me as a web developer for potential employers. I would like the background to be a dark color on the front for contrast with my logo and name. The back will have all my information along with a smaller version of the logo. I want something with a modern look and feel, not too conservative. This will be used for potential employers and freelance work.

Industry/Entity Type

Business

Contact Information for Business Card

Front should have my logo and name. The back should have all my personal information which would include: name: Tom Varulek, phone: 570-614-3098, email: tomvarulek@quillbox.net, website url: www.tomvarulek.net, logo, web developer.

Font styles to use
Sans Serif

Requirements
Must have
• Must include my logo. The color palette base color will be the logo color.

```html
<!DOCTYPE html>
<html lang="en">
<head>
<meta charset="utf-8">
<title>Tom Varulek — Business Card</title>
<link rel="stylesheet" href="https://fonts.googleapis.com/css2?family=Arimo:wght@400;700&display=swap">
<style>
  :root {
    --backdrop: #e9e6e1;
    --card-black: #0c0c0c;
    --card-charcoal: #1f1f1f;
    --brand-teal: #1f8c76;
    --brand-teal-light: #4fa891;
    --logo-mint: #6fcab8;
    --ink-white: #ffffff;
  }
  * { box-sizing: border-box; margin: 0; padding: 0; }
  html, body {
    width: 1200px; height: 892px; overflow: hidden;
    background: var(--backdrop);
    font-family: "Arimo", Arial, sans-serif;
  }
  .canvas { position: relative; width: 1200px; height: 892px; }

  .card {
    position: absolute;
    border-radius: 6px;
    overflow: hidden;
    box-shadow: 0 10px 24px rgba(0,0,0,.22);
  }

  /* Front */
  .card-front {
    left: 560px; top: 70px; width: 580px; height: 332px;
    background: linear-gradient(135deg, var(--card-black) 0%, var(--card-black) 55%, var(--card-charcoal) 100%);
  }
  .front-mark {
    position: absolute; left: 0; right: 0; top: 78px;
    display: flex; align-items: center; justify-content: center; gap: 16px;
  }
  .mark-ring {
    width: 46px; height: 46px; border-radius: 50%;
    border: 6px solid var(--logo-mint);
  }
  .mark-name {
    color: var(--logo-mint); font-weight: 700; font-size: 34px; letter-spacing: .5px;
  }
  .front-name {
    position: absolute; left: 0; right: 0; top: 212px; text-align: center;
    color: var(--ink-white); font-size: 44px; letter-spacing: 1px;
  }

  /* Back */
  .card-back {
    left: 60px; top: 440px; width: 620px; height: 354px;
    background: var(--card-black);
  }
  .card-back svg.wave { position: absolute; inset: 0; }
  .back-mark {
    position: absolute; left: 150px; top: 46px;
    display: flex; align-items: center; gap: 12px;
  }
  .back-mark .mark-ring { width: 34px; height: 34px; border-width: 5px; }
  .back-mark .mark-name { font-size: 26px; }
  .faint-ring {
    position: absolute; left: 450px; top: 150px;
    width: 110px; height: 110px; border-radius: 50%;
    border: 14px solid rgba(255,255,255,.12);
  }
  .identity {
    position: absolute; left: 30px; top: 200px; width: 235px; text-align: right;
    color: var(--ink-white);
  }
  .identity-name { font-size: 34px; line-height: 1.1; }
  .identity-role { font-size: 18px; margin-top: 4px; }
  .divider {
    position: absolute; left: 285px; top: 205px; width: 2px; height: 118px;
    background: var(--ink-white);
  }
  .contacts {
    position: absolute; left: 305px; top: 214px; list-style: none;
    color: var(--ink-white); font-size: 20px;
  }
  .contacts li { display: flex; align-items: center; gap: 12px; height: 34px; }
  .contacts svg { width: 16px; height: 16px; flex: none; }
</style>
</head>
<body>
<main class="canvas">

  <section class="card card-front" aria-label="Card front">
    <div class="front-mark">
      <span class="mark-ring"></span>
      <span class="mark-name">Tom Varulek</span>
    </div>
    <h1 class="front-name">TOM VARULEK</h1>
  </section>

  <section class="card card-back" aria-label="Card back">
    <svg class="wave" viewBox="0 0 620 354" width="620" height="354" aria-hidden="true">
      <defs>
        <linearGradient id="tealBand" x1="0" y1="0" x2="1" y2="1">
          <stop offset="0" stop-color="#1f8c76"/>
          <stop offset="1" stop-color="#4fa891"/>
        </linearGradient>
      </defs>
      <path d="M0,140 C180,170 330,190 440,205 C520,216 580,245 620,290 L620,354 L0,354 Z" fill="url(#tealBand)"/>
      <path d="M0,152 C180,182 330,202 440,217 C520,228 580,257 620,302" fill="none" stroke="#ffffff" stroke-width="3"/>
    </svg>

    <div class="back-mark">
      <span class="mark-ring"></span>
      <span class="mark-name">Tom Varulek</span>
    </div>
    <span class="faint-ring" aria-hidden="true"></span>

    <div class="identity">
      <p class="identity-name">Tom Varulek</p>
      <p class="identity-role">web developer</p>
    </div>
    <span class="divider" aria-hidden="true"></span>

    <ul class="contacts">
      <li>
        <svg viewBox="0 0 16 16" aria-hidden="true"><rect width="16" height="16" rx="2" fill="#fff"/><path d="M5 3.5h2l.8 2.5-1.3 1a6 6 0 0 0 2.5 2.5l1-1.3 2.5.8v2a1 1 0 0 1-1 1A8 8 0 0 1 4 4.5a1 1 0 0 1 1-1z" fill="#1f8c76"/></svg>
        570-614-3098
      </li>
      <li>
        <svg viewBox="0 0 16 16" aria-hidden="true"><rect width="16" height="16" rx="2" fill="#fff"/><rect x="3" y="4.5" width="10" height="7" fill="none" stroke="#1f8c76" stroke-width="1.4"/><path d="M3 4.5l5 4 5-4" fill="none" stroke="#1f8c76" stroke-width="1.4"/></svg>
        tomvarulek@quillbox.net
      </li>
      <li>
        <svg viewBox="0 0 16 16" aria-hidden="true"><rect width="16" height="16" rx="2" fill="#fff"/><circle cx="8" cy="8" r="4.5" fill="none" stroke="#1f8c76" stroke-width="1.3"/><path d="M3.5 8h9M8 3.5c-2 2.5-2 6.5 0 9M8 3.5c2 2.5 2 6.5 0 9" fill="none" stroke="#1f8c76" stroke-width="1"/></svg>
        www.tomvarulek.net
      </li>
    </ul>
  </section>

</main>
</body>
</html>
```